Brightwave Reach - Business Card

We need a business card for a Social Media Marketing company that specializes in online marketing for small businesses in Canada using common Social Media platforms such as Pixlora, Chatterly, Blinkpost & Quibber.

I have uploaded a copy of our logo which I would like utilized in the business card. We would like the business card to be modern yet classy design.

Our website is www.brightwavereach.ca

Industry/Entity Type

Marketing

Contact Information for Business Card

Email: info@brightwavereach.ca
Website: www.brightwavereach.ca
Telephone: 604-555-0193

Colors

Designer to choose colors to be used in the design.

Requirements
Must have
• Social Media icons on reverse
• Please add some designs with color.

```html
<!DOCTYPE html>
<html lang="en">
<head>
<meta charset="utf-8">
<title>Brightwave Reach – Business Card</title>
<link href="https://fonts.googleapis.com/css2?family=Oswald:wght@500;600&family=Open+Sans:wght@400;600&display=swap" rel="stylesheet">
<style>
  :root {
    --stage: #2b2b2d;
    --card-dark: #1d1d1f;
    --card-light: #ffffff;
    --silver: #a9abae;
    --ink: #353535;
    --slate: #6e8791;
    --rule: #4a4a4a;
  }
  * { box-sizing: border-box; margin: 0; padding: 0; }
  html, body {
    width: 1200px; height: 1000px; overflow: hidden;
    background: var(--stage);
  }
  .sheet {
    width: 1200px; height: 1000px;
    display: flex; flex-direction: column;
    align-items: center; justify-content: center; gap: 60px;
  }
  .card {
    width: 700px; height: 400px;
    border-radius: 4px;
    position: relative;
    box-shadow: 0 12px 30px rgba(0,0,0,.35);
  }
  /* Reverse side */
  .card--reverse {
    background: var(--card-dark);
    display: flex; flex-direction: column;
    align-items: center; justify-content: center;
  }
  .brand-name {
    font-family: "Oswald", sans-serif;
    font-weight: 600;
    font-size: 50px;
    letter-spacing: 1px;
    text-transform: uppercase;
    color: var(--silver);
    line-height: 1;
  }
  .social-row {
    position: absolute; bottom: 34px; left: 0; right: 0;
    display: flex; justify-content: center; gap: 18px;
    list-style: none;
    font-family: "Open Sans", sans-serif;
    font-weight: 600;
    font-size: 12px;
    color: var(--slate);
  }
  /* Front side */
  .card--front {
    background: var(--card-light);
    display: flex; align-items: center;
  }
  .identity {
    width: 300px; text-align: right; padding-right: 18px;
  }
  .identity__name {
    font-family: "Oswald", sans-serif;
    font-weight: 600;
    font-size: 31px;
    letter-spacing: 1px;
    color: var(--ink);
    line-height: 1.1;
  }
  .identity__title {
    font-family: "Open Sans", sans-serif;
    font-weight: 600;
    font-size: 19px;
    letter-spacing: 1px;
    color: var(--slate);
    line-height: 1.1;
  }
  .divider {
    width: 1px; height: 62px; background: var(--rule);
  }
  .contacts {
    list-style: none;
    padding-left: 18px;
    font-family: "Open Sans", sans-serif;
    font-size: 16px;
    color: var(--ink);
  }
  .contacts li {
    display: flex; align-items: center; gap: 12px;
    line-height: 1.6;
  }
  .contacts svg { width: 13px; height: 13px; fill: var(--slate); flex: none; }
</style>
</head>
<body>
<main class="sheet">
  <section class="card card--reverse" aria-label="Card reverse">
    <h1 class="brand-name">Brightwave Reach</h1>
    <ul class="social-row">
      <li>Chatterly</li>
      <li>Quibber</li>
      <li>Pixlora</li>
      <li>Blinkpost</li>
    </ul>
  </section>

  <section class="card card--front" aria-label="Card front">
    <div class="identity">
      <p class="identity__name">DANA WHITLOCK</p>
      <p class="identity__title">Precedent</p>
    </div>
    <span class="divider"></span>
    <ul class="contacts">
      <li>
        <svg viewBox="0 0 24 24" aria-hidden="true"><path d="M6.6 10.8a15.1 15.1 0 0 0 6.6 6.6l2.2-2.2c.3-.3.7-.4 1-.2 1.1.4 2.3.6 3.6.6.6 0 1 .4 1 1V20c0 .6-.4 1-1 1A17 17 0 0 1 3 4c0-.6.4-1 1-1h3.5c.6 0 1 .4 1 1 0 1.3.2 2.5.6 3.6.1.3 0 .7-.2 1z"/></svg>
        <span>604-555-0193</span>
      </li>
      <li>
        <svg viewBox="0 0 24 24" aria-hidden="true"><path d="M2 5h20v14H2z" fill="none"/><path d="M2 5h20v14H2V5zm2 2v.4l8 5 8-5V7H4zm0 2.8V17h16V9.8l-8 5-8-5z"/></svg>
        <span>info@brightwavereach.ca</span>
      </li>
      <li>
        <svg viewBox="0 0 24 24" aria-hidden="true"><circle cx="12" cy="12" r="10"/><path d="M2 12h20M12 2c3 3 3 17 0 20M12 2c-3 3-3 17 0 20" stroke="#fff" stroke-width="1.4" fill="none"/></svg>
        <span>www.brightwavereach.ca</span>
      </li>
    </ul>
  </section>
</main>
</body>
</html>
```